Meridale Real Estate

We are looking for help with web design for a new company that is revolutionizing the real estate world on the listing side: by charing per hour for top level professional real estate services. We would like the concept to be simple, clean and easily understood.
Updates

We want this website to actually function, not just a static design.

Industry/Entity Type

Real Estate

```html
<!DOCTYPE html>
<html lang="en">
<head>
<meta charset="utf-8">
<title>Meridale Real Estate</title>
<link href="https://fonts.googleapis.com/css2?family=Open+Sans:wght@400;600;700&family=Oswald:wght@400;500&display=swap" rel="stylesheet">
<style>
:root{
  --ink:#333;
  --muted:#777;
  --line:#e2e2e2;
  --blue:#4aa3c9;
  --blue-dark:#3a86a8;
  --link:#3d9bc4;
  --star:#f08a1c;
  --star-off:#222;
  --panel:#fff;
  --page:#f4f4f4;
  --footer:#3b3b3b;
  --footer-text:#cfcfcf;
}
*{box-sizing:border-box;margin:0;padding:0}
html,body{width:1200px;height:3284px;overflow:hidden}
body{position:relative;background:var(--page);font-family:"Open Sans",Arial,sans-serif;color:var(--ink);font-size:13px}
.abs{position:absolute}
a{color:inherit;text-decoration:none}

/* top bar */
.topbar{left:0;top:0;width:1200px;height:45px;background:#fff;border-bottom:1px solid var(--line)}
.topbar .email{left:48px;top:14px;font-size:12px;color:var(--muted);display:flex;align-items:center;gap:8px}
.topbar .account{left:775px;top:14px;font-size:11px;color:var(--muted);display:flex;gap:22px}
.topbar .social{left:900px;top:0;height:45px;display:flex}
.topbar .social span{width:56px;height:45px;border-left:1px solid var(--line);display:flex;align-items:center;justify-content:center}
.topbar .social span i{width:12px;height:12px;border-radius:50%;background:#999;display:block}

/* header */
.header{left:0;top:45px;width:1200px;height:112px;background:#fff}
.brand{left:60px;top:32px;font-weight:600;font-size:19px;color:var(--ink);letter-spacing:.5px}
.nav{left:372px;top:78px;display:flex;gap:28px;font-size:14px;color:var(--ink)}
.phone{left:935px;top:61px;width:247px;height:51px;background:var(--blue);display:flex;align-items:center;color:#fff}
.phone .ico{width:51px;height:51px;background:var(--blue-dark);display:flex;align-items:center;justify-content:center}
.phone .num{flex:1;text-align:center;font-size:22px;letter-spacing:.5px}

/* hero */
.hero{left:0;top:157px;width:1200px;height:419px;background:linear-gradient(180deg,#b8d6ea 0%,#9cbfd8 18%,#8a5a44 30%,#9a7a5e 55%,#a99580 72%,#5f8b3c 85%,#3f6e2a 100%)}
.hero-title{left:157px;top:308px;width:420px;height:58px;background:rgba(255,255,255,.6);font-size:36px;line-height:42px;padding:8px 14px;color:#333}
.hero-sub{left:157px;top:368px;width:510px;height:36px;background:rgba(0,0,0,.45);color:#fff;font-size:15px;line-height:22px;padding:7px 14px}

/* search */
.search{left:45px;top:606px;width:1097px;height:164px;background:var(--panel);box-shadow:0 1px 4px rgba(0,0,0,.12)}
.field{position:absolute}
.field label{display:block;font-size:12px;color:#555;margin-bottom:8px}
.field .select{height:30px;border:1px solid #d6d6d6;background:#fff;font-size:12px;color:#555;padding:6px 8px;position:relative}
.field .select::after{content:"";position:absolute;right:0;top:0;width:26px;height:28px;border-left:1px solid #d6d6d6;background:#f5f5f5}
.search .btn{left:975px;top:122px;width:90px;height:32px;background:var(--blue);color:#fff;font-size:13px;text-align:center;line-height:32px}

/* section heading */
.sec-title{font-size:16px;font-weight:600;letter-spacing:.5px;color:#333}
.arrows{display:flex;gap:6px}
.arrows span{width:20px;height:20px;background:var(--blue);display:flex;align-items:center;justify-content:center}

/* property cards */
.card{top:846px;width:350px;height:417px;background:#fff;box-shadow:0 1px 3px rgba(0,0,0,.1)}
.card .photo{position:absolute;left:0;top:0;width:350px;height:197px}
.card .tag{position:absolute;left:0;top:0;background:rgba(255,255,255,.85);font-size:11px;padding:4px 8px;color:#444}
.card .price{position:absolute;right:0;top:170px;background:rgba(60,60,60,.85);color:#fff;font-size:11px;padding:6px 10px}
.card h3{position:absolute;left:22px;top:213px;width:300px;font-size:16px;font-weight:600;line-height:22px;text-transform:uppercase;color:#333}
.card .row{position:absolute;left:22px;width:306px;height:36px;border-top:1px solid var(--line);display:flex;justify-content:space-between;align-items:center;font-size:12px;font-weight:600}
.star-on{fill:var(--star)}
.star-off{fill:var(--star-off)}

/* map */
.map{left:0;top:1293px;width:1200px;height:387px;background:linear-gradient(135deg,#e9e3d4 0%,#efe9dc 40%,#e6ddc8 70%,#dfe6d2 100%)}

/* about */
.about h2{font-size:16px;font-weight:600}
.about p{font-size:12px;line-height:17px;color:#555}
.badge{width:160px;height:50px;background:#111;border-radius:7px}
.feature h4{font-size:15px;font-weight:600;color:#333;letter-spacing:.3px}
.feature p{font-size:12px;line-height:17px;color:#555;margin-top:10px}
.more{color:var(--link)}

/* calendar */
.calendar{left:0;top:2059px;width:1200px;height:328px;background:linear-gradient(135deg,#6fb4d2 0%,#5ea8c9 50%,#72b8d6 100%)}
.cal-head{left:160px;top:2078px;display:flex;align-items:center;gap:16px}
.cal-title{font-family:"Oswald",sans-serif;font-weight:400;font-size:31px;line-height:44px;color:#fff;letter-spacing:.5px}
.cal-arrows{display:flex;gap:10px}
.cal-arrows span{width:28px;height:28px;border-radius:50%;border:1px solid #fff;display:flex;align-items:center;justify-content:center}
.events{left:160px;top:2150px;width:655px;background:#fff;box-shadow:0 2px 6px rgba(0,0,0,.15)}
.event{height:70px;border-bottom:1px solid var(--line);display:flex;align-items:center}
.event:last-child{border-bottom:none}
.event .date{width:78px;height:70px;border-right:1px solid var(--line);display:flex;align-items:center;justify-content:center;gap:4px;font-family:"Oswald",sans-serif;color:#888}
.event .date b{font-size:24px;font-weight:500}
.event .date small{font-size:11px;line-height:13px}
.event .info{padding-left:14px}
.event h5{font-family:"Oswald",sans-serif;font-weight:400;font-size:19px;color:#555}
.event .meta{font-size:10px;color:#999;margin-top:2px}

/* news */
.news{top:2530px;width:316px}
.news .photo{width:316px;height:182px;border:5px solid #ddd}
.news .date{font-size:12px;color:#666;margin-top:25px}
.news .title{font-size:13px;color:var(--link);margin-top:14px}
.news p{font-size:12px;line-height:18px;color:#666;margin-top:12px}
.news .read{font-size:12px;color:#333;margin-top:14px}

/* footer */
.footer{left:0;top:3006px;width:1200px;height:278px;background:var(--footer);color:var(--footer-text)}
.footer h6{font-size:11px;font-weight:600;letter-spacing:.5px;color:#ddd}
.footer p{font-size:12px;line-height:18px}
.footer ul{list-style:none;font-size:12px;line-height:28px}
.footer .icons{display:flex;gap:10px}
.footer .icons i{width:18px;height:18px;border-radius:50%;background:#ddd;display:block}
.locator-btn{width:200px;height:45px;background:#d8d8d8;border-radius:3px;color:#333;font-size:11px;font-weight:700;display:flex;align-items:center;gap:10px;padding-left:14px}
</style>
</head>
<body>

<svg width="0" height="0" style="position:absolute">
  <defs><path id="star" d="M8 0l2.4 5 5.6.8-4 3.9.9 5.5L8 12.6 3.1 15.2 4 9.7 0 5.8 5.6 5z"/></defs>
</svg>

<!-- top bar -->
<div class="abs topbar">
  <div class="abs email">
    <svg width="14" height="10" viewBox="0 0 14 10"><rect x=".5" y=".5" width="13" height="9" fill="none" stroke="#999"/><path d="M.5 .5 7 6 13.5 .5" fill="none" stroke="#999"/></svg>
    Email us at : info@meridalehomes.com
  </div>
  <div class="abs account"><a>&#9679; Login</a><a>Register</a></div>
  <div class="abs social"><span><i></i></span><span><i></i></span><span><i></i></span><span><i></i></span><span><i></i></span></div>
</div>

<!-- header -->
<header class="abs header">
  <div class="abs brand">Meridale Real Estate</div>
  <nav class="abs nav"><a>Home</a><a>Listing</a><a>News</a><a>IDX</a><a>Gallery</a><a>Blog</a><a>Types</a><a>Contact us</a></nav>
  <div class="abs phone">
    <span class="ico"><svg width="20" height="20" viewBox="0 0 24 24"><path fill="#fff" d="M6.6 10.8a15 15 0 0 0 6.6 6.6l2.2-2.2c.3-.3.7-.4 1-.2 1.1.4 2.3.6 3.6.6.6 0 1 .4 1 1V20c0 .6-.4 1-1 1A17 17 0 0 1 3 4c0-.6.4-1 1-1h3.5c.6 0 1 .4 1 1 0 1.3.2 2.5.6 3.6.1.3 0 .7-.2 1z"/></svg></span>
    <span class="num">1-800-555-0142</span>
  </div>
</header>

<!-- hero -->
<section class="abs hero" role="img" aria-label="Photo of a two-storey suburban family house with a stone porch, lawn and flower beds"></section>
<div class="abs hero-title">Lorem Ipsum</div>
<div class="abs hero-sub">Nemo enim ipsam voluptatem quia voluptas sit aspernatur.</div>

<!-- search -->
<form class="abs search">
  <div class="field" style="left:30px;top:22px;width:245px"><label>Property ID</label><div class="select">Any</div></div>
  <div class="field" style="left:292px;top:22px;width:245px"><label>Property Location</label><div class="select">Any</div></div>
  <div class="field" style="left:555px;top:22px;width:245px"><label>Property Status</label><div class="select">Any</div></div>
  <div class="field" style="left:818px;top:22px;width:248px"><label>Property Type</label><div class="select">Any</div></div>
  <div class="field" style="left:30px;top:93px;width:140px"><label>MinBeds</label><div class="select">Any</div></div>
  <div class="field" style="left:187px;top:93px;width:140px"><label>MedBaths</label><div class="select">Any</div></div>
  <div class="field" style="left:345px;top:93px;width:140px"><label>MinPrice</label><div class="select">Any</div></div>
  <div class="field" style="left:503px;top:93px;width:140px"><label>MaxPrice</label><div class="select">Any</div></div>
  <div class="field" style="left:661px;top:93px;width:140px"><label>MinArea(SqFt)</label><div class="select">Any</div></div>
  <div class="field" style="left:819px;top:93px;width:140px"><label>MaxArea(SqFt)</label><div class="select">Any</div></div>
  <div class="abs btn">Search</div>
</form>

<!-- properties -->
<h2 class="abs sec-title" style="left:45px;top:796px">PROPERTIES</h2>
<a class="abs more" style="left:1030px;top:800px;font-size:12px">View All</a>
<div class="abs arrows" style="left:1096px;top:798px">
  <span><svg width="8" height="10"><path d="M6 1 2 5l4 4" stroke="#fff" stroke-width="2" fill="none"/></svg></span>
  <span><svg width="8" height="10"><path d="M2 1l4 4-4 4" stroke="#fff" stroke-width="2" fill="none"/></svg></span>
</div>

<article class="abs card" style="left:45px">
  <div class="photo" role="img" aria-label="Photo of a modern white villa with glass walls at dusk" style="background:linear-gradient(180deg,#9fb6c9,#e0d2b4 55%,#6c8a4f)"></div>
  <span class="tag">For Rent</span><span class="price">$ 16,600/month</span>
  <h3>5299 At Vero Eos Et Accusamus, ET 33140</h3>
  <div class="row" style="top:285px"><span>Bedrooms</span><span>3</span></div>
  <div class="row" style="top:321px"><span>Bathrooms</span><span>3</span></div>
  <div class="row" style="top:357px"><span>Reviews</span>
    <svg width="88" height="16" viewBox="0 0 88 16"><use href="#star" class="star-on"/><use href="#star" x="24" class="star-on"/><use href="#star" x="48" class="star-on"/><use href="#star" x="72" class="star-off"/></svg></div>
</article>

<article class="abs card" style="left:417px">
  <div class="photo" role="img" aria-label="Photo of a resort apartment complex with a blue swimming pool" style="background:linear-gradient(180deg,#4f8fd0,#9fc1de 35%,#c79a6a 60%,#3aa5c8)"></div>
  <span class="tag">For Rent</span><span class="price">$ 19,750/month</span>
  <h3>1680 At Vero Eos Et Accusamus, ET 33139 FL</h3>
  <div class="row" style="top:285px"><span>Bedrooms</span><span>4</span></div>
  <div class="row" style="top:321px"><span>Bathrooms</span><span>2</span></div>
  <div class="row" style="top:357px"><span>Reviews</span>
    <svg width="88" height="16" viewBox="0 0 88 16"><use href="#star" class="star-on"/><use href="#star" x="24" class="star-on"/><use href="#star" x="48" class="star-on"/><use href="#star" x="72" class="star-on"/></svg></div>
</article>

<article class="abs card" style="left:793px">
  <div class="photo" role="img" aria-label="Photo of a white colonial-style house with columns and a lawn" style="background:linear-gradient(180deg,#8fb7dd,#dfe3e6 45%,#b9b8b0 70%,#5e8a44)"></div>
  <span class="tag">For Rent</span><span class="price">$ 18,500/month</span>
  <h3>4203 At Vero Eos Et Accusamus, ET 40110 FL</h3>
  <div class="row" style="top:285px"><span>Bedrooms</span><span>4</span></div>
  <div class="row" style="top:321px"><span>Bathrooms</span><span>3</span></div>
  <div class="row" style="top:357px"><span>Reviews</span>
    <svg width="88" height="16" viewBox="0 0 88 16"><use href="#star" class="star-on"/><use href="#star" x="24" class="star-on"/><use href="#star" x="48" class="star-on"/><use href="#star" x="72" class="star-on"/></svg></div>
</article>

<!-- map -->
<section class="abs map" role="img" aria-label="Street map of the coastal city showing property locations with pins"></section>

<!-- about -->
<section class="about">
  <h2 class="abs" style="left:45px;top:1730px">ABOUT US</h2>
  <p class="abs" style="left:45px;top:1768px;width:345px">Lorem ipsum dolor sit amet consectetur incididunt ut labore et dolore magna aliqua adipisicing elit seddo eiusmod tempor.<br>Sed perspiciatis unde omnisiste natus error voluptatem remopa accusantium doloremque laudantium, totam rem aperiam.</p>
  <p class="abs" style="left:45px;top:1906px;width:345px">At vero eos et accusamus et iusto odio dignissimos ducimus qui blanditiis praesentium voluptatum deleniti atque corrupti quos dolores et quas molestias excepturi sint occaecati cupiditate non providen.</p>
  <a class="abs more" style="left:45px;top:1992px;font-size:12px">Continue »</a>

  <div class="abs badge" style="left:598px;top:1766px" role="img" aria-label="Mobile app download badge"></div>
  <div class="abs badge" style="left:797px;top:1766px" role="img" aria-label="Second mobile app download badge"></div>

  <div class="abs feature" style="left:475px;top:1885px;width:300px">
    <svg class="abs" style="left:0;top:0" width="22" height="34" viewBox="0 0 22 34"><path d="M11 0C5 0 0 5 0 11c0 8 11 19 11 19s11-11 11-19C22 5 17 0 11 0z" fill="#4aa3c9"/><circle cx="11" cy="11" r="4" fill="#fff"/></svg>
    <h4 style="margin-left:40px;margin-top:8px">APARTMENT LOCATOR</h4>
    <p style="margin-left:40px">Lorem ipsum dolor sit amet consectetur incididunt ut labore et dolore magna aliqua adipisicing elit seddo eiusmod tempor. <span class="more">Continue »</span></p>
  </div>
  <div class="abs feature" style="left:842px;top:1880px;width:300px">
    <svg class="abs" style="left:0;top:0" width="40" height="40" viewBox="0 0 40 40"><path d="M4 10 20 4v30L4 38z" fill="#8cc3dc"/><path d="M20 4l16 4v28l-16-2z" fill="#4aa3c9"/></svg>
    <h4 style="margin-left:58px;margin-top:13px">VIEW ONLINE MAGAZINES</h4>
    <p style="margin-top:18px">Lorem ipsum dolor sit amet consectetur incididunt ut labore et dolore magna aliqua adipisicing elit seddo eiusmod tempor. <span class="more">Continue »</span></p>
  </div>
</section>

<!-- calendar -->
<section class="abs calendar" role="img" aria-label="Soft blue-tinted photo of a bright apartment interior"></section>
<div class="abs cal-head">
  <h2 class="cal-title">CALENDAR - APRIL , 2014</h2>
  <div class="cal-arrows">
    <span><svg width="8" height="10"><path d="M6 1 2 5l4 4" stroke="#fff" stroke-width="1.5" fill="none"/></svg></span>
    <span><svg width="8" height="10"><path d="M2 1l4 4-4 4" stroke="#fff" stroke-width="1.5" fill="none"/></svg></span>
  </div>
</div>
<div class="abs events">
  <div class="event"><div class="date"><b>20</b><small>//<br>MAR</small></div><div class="info"><h5>LOREM IPSUM DOLOR SIT AMET</h5><div class="meta">9:00 am · Open house · Main Street office · seats left</div></div></div>
  <div class="event"><div class="date"><b>18</b><small>10<br>APR</small></div><div class="info"><h5>LOREM IPSUM DOLOR SIT AMET</h5><div class="meta">1:30 pm · Buyer seminar · Harbor room</div></div></div>
  <div class="event"><div class="date"><b>10</b><small>18<br>APR</small></div><div class="info"><h5>LOREM IPSUM DOLOR SIT AMET</h5><div class="meta">4:00 pm · Agent meetup · Lobby</div></div></div>
</div>

<!-- what's new -->
<h2 class="abs sec-title" style="left:60px;top:2478px;font-size:15px">WHAT'S NEW</h2>
<div class="abs arrows" style="left:1091px;top:2476px">
  <span><svg width="8" height="10"><path d="M6 1 2 5l4 4" stroke="#fff" stroke-width="2" fill="none"/></svg></span>
  <span><svg width="8" height="10"><path d="M2 1l4 4-4 4" stroke="#fff" stroke-width="2" fill="none"/></svg></span>
</div>

<article class="abs news" style="left:58px">
  <div class="photo" role="img" aria-label="Photo of a sunlit white living room with lounge chairs" style="background:linear-gradient(135deg,#f2f2ef,#cfd6d8 50%,#b2a58f)"></div>
  <div class="date">April 03,2014</div>
  <div class="title">Lorem ipsum dolor sit amet.</div>
  <p>Excepteur sint occaecat cupidatat non proident, sunt in culpa qui officia deserunt mollit anim id est laborum.</p>
  <div class="read">Read more »</div>
</article>
<article class="abs news" style="left:419px">
  <div class="photo" role="img" aria-label="Photo of a hotel bedroom with a city view window" style="background:linear-gradient(135deg,#6f8fa8,#d9cfc0 50%,#7a5a3f)"></div>
  <div class="date">Mar 16,2014</div>
  <div class="title">Lorem ipsum dolor sit amet.</div>
  <p>Excepteur sint occaecat cupidatat non proident, sunt in culpa qui officia deserunt mollit anim id est laborum.</p>
  <div class="read">Read more »</div>
</article>
<article class="abs news" style="left:793px">
  <div class="photo" role="img" aria-label="Photo of a warm living room with a cream sofa and dark furniture" style="background:linear-gradient(135deg,#5a4030,#cbb9a0 50%,#3e2a20)"></div>
  <div class="date">Mar 25,2014</div>
  <div class="title">Lorem ipsum dolor sit amet.</div>
  <p>Excepteur sint occaecat cupidatat non proident, sunt in culpa qui officia deserunt mollit anim id est laborum.</p>
  <div class="read">Read more »</div>
</article>

<!-- footer -->
<footer class="abs footer">
  <div class="abs" style="left:45px;top:35px;width:300px">
    <h6>FIND APARTMENTS FOR RENT</h6>
    <p style="margin-top:18px">Apartments for Rent | An Apartment Finder &amp; Guide for Rentals</p>
    <p style="margin-top:16px">Lorem ipsum dolor sit amet, consectetur adipisicing elit, sed do eiusmod tempor incididunt ut labore et dolore magna aliqua. Ut enim ad minim veniam.</p>
  </div>
  <div class="abs" style="left:513px;top:35px">
    <h6>SITE LINKS</h6>
    <ul style="margin-top:10px"><li>Home</li><li>Managers &amp; Owners</li><li>About Us</li><li>Advertise</li><li>Privacy Policy</li><li>Contact Us</li></ul>
  </div>
  <div class="abs" style="left:793px;top:35px">
    <h6>FOLLOW US</h6>
    <div class="icons" style="margin-top:22px"><i></i><i></i><i></i><i></i><i></i></div>
    <div class="locator-btn" style="margin-top:70px">
      <svg width="20" height="20" viewBox="0 0 20 20"><circle cx="8" cy="8" r="6" fill="none" stroke="#333" stroke-width="2.5"/><path d="M12.5 12.5 18 18" stroke="#333" stroke-width="3"/></svg>
      APARTMENT LOCATOR
    </div>
  </div>
</footer>

</body>
</html>
```